RWT Fittings Ltd Business Cards

We need a business card with our business logo. We provide window and door installations on high-rises in west coast British Colombia, Canada.

I would like my business information and details on one side of the card, and the other side the company name with logo

Target Market(s)

General Contractors

Industry/Entity Type

Construction

Contact Information for Business Card

one side i want my company name and logo in the dark theme logo that i provided

Requirements
Must have
• Marco Peltieri, 16045518293, RWTFittings@mailbox-demo.com, 1407-5194 Linden Row Burnaby BC, V5H 2K9, Owner & Manager

```html
<!DOCTYPE html>
<html lang="en">
<head>
<meta charset="utf-8">
<title>RWT Fittings Ltd – Business Cards</title>
<link rel="stylesheet" href="https://fonts.googleapis.com/css2?family=Josefin+Sans:wght@300;400&family=Michroma&display=swap">
<style>
  :root {
    --page-bg: #ececec;
    --card-dark: #231f20;
    --card-dark-top: #3d3c3f;
    --brand-blue: #3aaee3;
    --brand-grey: #9c9c9e;
    --text-light: #c9c9c9;
    --rule: #bdbdbd;
  }
  * { margin: 0; padding: 0; box-sizing: border-box; }
  html, body {
    width: 1200px;
    height: 1000px;
    overflow: hidden;
    background: var(--page-bg);
  }
  .card {
    position: absolute;
    top: 204px;
    width: 338px;
    height: 592px;
    overflow: hidden;
  }
  .card--contact {
    left: 209px;
    background: var(--card-dark);
    text-align: center;
    color: var(--text-light);
    font-family: "Josefin Sans", sans-serif;
    font-weight: 300;
  }
  .card--brand {
    left: 653px;
    background: linear-gradient(160deg, var(--card-dark-top) 0%, var(--card-dark) 55%);
  }

  .brand-lockup {
    position: absolute;
    left: 0;
    right: 0;
    top: 58px;
    display: flex;
    align-items: center;
    justify-content: center;
    gap: 10px;
  }
  .brand-lockup__mark {
    width: 22px;
    height: 22px;
    background: var(--brand-blue);
  }
  .brand-lockup__name {
    font-family: "Michroma", sans-serif;
    font-size: 17px;
    color: var(--brand-blue);
    text-transform: uppercase;
    white-space: nowrap;
  }

  .person {
    position: absolute;
    left: 42px;
    right: 42px;
    top: 256px;
  }
  .person__name {
    font-family: "Michroma", sans-serif;
    font-size: 23px;
    color: var(--brand-blue);
    letter-spacing: 0.5px;
    line-height: 1;
    padding-bottom: 12px;
    border-bottom: 1px solid var(--rule);
    white-space: nowrap;
  }
  .person__role {
    margin-top: 10px;
    font-size: 18px;
  }

  .contact {
    position: absolute;
    left: 0;
    right: 0;
    top: 432px;
    font-size: 16.5px;
    line-height: 19px;
  }
  .contact__phone { margin-top: 30px; }
  .contact__email { margin-top: 6px; }

  .brand-title {
    position: absolute;
    left: 0;
    right: 0;
    top: 52px;
    text-align: center;
    font-family: "Michroma", sans-serif;
    font-size: 27px;
    line-height: 1.25;
    color: var(--brand-blue);
    text-transform: uppercase;
  }
  .brand-art {
    position: absolute;
    left: 0;
    bottom: 0;
    width: 338px;
    height: 378px;
    display: block;
  }
</style>
</head>
<body>

  <section class="card card--contact">
    <div class="brand-lockup">
      <span class="brand-lockup__mark"></span>
      <span class="brand-lockup__name">RWT Fittings Ltd</span>
    </div>

    <div class="person">
      <h1 class="person__name">SAMPLE NAME</h1>
      <p class="person__role">CEO/Founder</p>
    </div>

    <address class="contact" style="font-style: normal;">
      <p>123 Street Name, Suite 456</p>
      <p>Country Name, State 78901</p>
      <p class="contact__phone">+123-456-7890</p>
      <p class="contact__email">samplename@rwtfittingsltd.com</p>
    </address>
  </section>

  <section class="card card--brand">
    <h2 class="brand-title">RWT Fittings<br>Ltd</h2>
    <svg class="brand-art" viewBox="0 0 338 378" role="img" aria-label="Large decorative building motif in grey and blue">
      <defs>
        <linearGradient id="brandArtFill" x1="0" y1="0" x2="1" y2="0">
          <stop offset="0" stop-color="#9c9c9e"/>
          <stop offset="0.45" stop-color="#8e9aa3"/>
          <stop offset="0.75" stop-color="#3aaee3"/>
          <stop offset="1" stop-color="#3aaee3"/>
        </linearGradient>
      </defs>
      <polygon points="0,60 338,0 338,378 0,378" fill="url(#brandArtFill)"/>
    </svg>
  </section>

</body>
</html>
```